Tallon Electrical Business Card

We need a business card design for our family-run electrical contracting business based in Western Australia called 'Tallon Electrical'. We provide electrical services including residential, commercial and industrial. We aim for individual business cards to be made for all of our employees. We already have a company logo, which we require to be featured on the design. We would like simple, sleek and vibrant designs, which incorporate our logo and represent our business. We do not want anything involving too many graphics/images. We like the colours red, black, white and all shades of grey. The final design should communicate professionalism and trustworthiness.
We require the following contact information:
Name- Grant Pellow
EC 5871
Mobile number- 0455 870 219
Fax number (including area code)- (08) 9560 2831
Email adress- name@tallonelectrical.com.au
Electrical
- ITC Handel Bold

```html
<!DOCTYPE html>
<html lang="en">
<head>
<meta charset="utf-8">
<title>Tallon Electrical Business Card</title>
<link rel="stylesheet" href="https://fonts.googleapis.com/css2?family=Open+Sans:wght@400;700&family=Saira+Semi+Condensed:wght@500&display=swap">
<style>
  :root {
    --bg: #1c1c1e;
    --card: #ffffff;
    --card-shade: #e6e6e6;
    --ink: #2b2b2b;
    --ink-soft: #555555;
    --rule: #9a9a9a;
    --red: #d3141c;
    --red-deep: #8e0a10;
    --grey-band: #3a3a3c;
    --faint: rgba(211, 20, 28, 0.08);
  }
  * { margin: 0; padding: 0; box-sizing: border-box; }
  html, body { width: 1200px; height: 871px; overflow: hidden; }
  body { background: var(--bg); font-family: "Open Sans", sans-serif; position: relative; }

  .card {
    position: absolute;
    left: 290px;
    width: 620px;
    height: 378px;
    overflow: hidden;
    background: linear-gradient(135deg, var(--card) 0%, var(--card) 55%, var(--card-shade) 100%);
  }
  .card--back { top: 40px; display: flex; align-items: center; justify-content: center; }
  .card--front { top: 452px; }

  .brand { display: flex; align-items: center; gap: 10px; }
  .brand__mark { width: 22px; height: 22px; background: var(--red); }
  .brand__name {
    font-family: "Open Sans", sans-serif;
    font-weight: 700;
    font-size: 24px;
    letter-spacing: 1px;
    text-transform: uppercase;
    color: var(--ink);
  }
  .card--front .brand { position: absolute; top: 40px; right: 36px; }
  .card--front .brand__name { font-size: 20px; }
  .card--front .brand__mark { width: 18px; height: 18px; }

  .decor-square {
    position: absolute; left: 40px; top: 40px;
    width: 200px; height: 200px; background: var(--faint);
  }

  .rule { position: absolute; height: 1px; background: var(--rule); }
  .rule--name { top: 110px; left: 0; width: 310px; }
  .rule--details { top: 186px; left: 300px; width: 284px; }

  .holder {
    position: absolute; top: 116px; left: 40px;
    font-family: "Saira Semi Condensed", sans-serif;
    font-weight: 500; font-size: 22px; letter-spacing: 5px;
    text-transform: uppercase; color: var(--ink);
  }
  .licence { position: absolute; top: 160px; left: 306px; font-size: 13px; letter-spacing: 1px; color: var(--ink); }

  .contacts { position: absolute; top: 200px; left: 300px; list-style: none; }
  .contacts li { display: flex; align-items: center; gap: 14px; height: 28px; font-size: 14px; letter-spacing: 1px; color: var(--ink-soft); }
  .contacts svg { width: 16px; height: 16px; flex: none; }

  .bands { position: absolute; left: 0; bottom: 0; width: 620px; height: 90px; }
</style>
</head>
<body>
  <section class="card card--back" aria-label="Card back">
    <div class="brand">
      <span class="brand__mark"></span>
      <span class="brand__name">Tallon Electrical</span>
    </div>
  </section>

  <section class="card card--front" aria-label="Card front">
    <div class="decor-square"></div>
    <div class="brand">
      <span class="brand__mark"></span>
      <span class="brand__name">Tallon Electrical</span>
    </div>

    <div class="rule rule--name"></div>
    <p class="holder">Grant Pellow</p>

    <p class="licence">EC 5871</p>
    <div class="rule rule--details"></div>

    <ul class="contacts">
      <li>
        <svg viewBox="0 0 16 16" aria-hidden="true"><rect x="4" y="1" width="8" height="14" rx="1.5" fill="none" stroke="#d3141c" stroke-width="1.4"/><line x1="7" y1="12.5" x2="9" y2="12.5" stroke="#d3141c" stroke-width="1.4"/></svg>
        <span>0455 870 219</span>
      </li>
      <li>
        <svg viewBox="0 0 16 16" aria-hidden="true"><rect x="4" y="1.5" width="8" height="4" fill="none" stroke="#d3141c" stroke-width="1.4"/><rect x="1.5" y="6" width="13" height="6" rx="1" fill="#d3141c"/><rect x="4" y="10" width="8" height="4.5" fill="#fff" stroke="#d3141c" stroke-width="1.4"/></svg>
        <span>(08) 9560 2831</span>
      </li>
      <li>
        <svg viewBox="0 0 16 16" aria-hidden="true"><rect x="1.5" y="3.5" width="13" height="9" fill="none" stroke="#d3141c" stroke-width="1.4"/><polyline points="1.5,3.5 8,9 14.5,3.5" fill="none" stroke="#d3141c" stroke-width="1.4"/></svg>
        <span>name@tallonelectrical.com.au</span>
      </li>
    </ul>

    <svg class="bands" viewBox="0 0 620 90" aria-hidden="true">
      <defs>
        <linearGradient id="redFade" x1="0" y1="0" x2="0" y2="1">
          <stop offset="0" stop-color="#d3141c"/>
          <stop offset="1" stop-color="#8e0a10"/>
        </linearGradient>
      </defs>
      <polygon points="0,14 248,14 272,40 0,40" fill="#3a3a3c"/>
      <polygon points="282,40 620,40 620,90 318,90" fill="url(#redFade)"/>
    </svg>
  </section>
</body>
</html>
```